SOLVE Study flyer

I need help designing a flyer for a research study that will include brain imaging in adolescents. The info is in the attached document. The study is called the Sequoia Outlook Lantern Valley Echo (SOLVE) study. Ideally this would be returned as a document that I can edit in the future as we will have several new recruitment phases (different age groups, etc. I also would love to have a logo designed as part of this project, but I recognize that might be a separate design request.

```html
<!DOCTYPE html>
<html lang="en">
<head>
<meta charset="utf-8">
<title>SOLVE Study Flyer</title>
<link href="https://fonts.googleapis.com/css2?family=Inter:wght@300;400;500;700;800&family=Playfair+Display:wght@400;700&display=swap" rel="stylesheet">
<style>
  :root{
    --navy:#0c2350;
    --navy-deep:#071a3f;
    --gold:#9b7439;
    --gold-light:#e9c47f;
    --ink:#12213f;
    --wall-light:#e8e6e6;
    --wall-dark:#cfd0d6;
    --white:#ffffff;
  }
  *{box-sizing:border-box;margin:0;padding:0}
  html,body{width:927px;height:1200px;overflow:hidden;background:var(--white)}
  .flyer{position:relative;width:927px;height:1200px;overflow:hidden;font-family:"Inter",sans-serif;color:var(--ink)}
  .serif{font-family:"Playfair Display",serif;font-variant-numeric:lining-nums}
  .hero-photo{position:absolute;left:0;top:0;width:927px;height:440px;
    background:radial-gradient(ellipse 210px 260px at 720px 230px,#8a8e99 0%,#b6b8bf 45%,rgba(214,214,219,0) 100%),
               linear-gradient(180deg,var(--wall-light) 0%,var(--wall-dark) 100%)}
  .backdrop{position:absolute;left:0;top:0}
  .brand{position:absolute;left:0;width:512px;text-align:center}
  .brand-name{top:48px;font-weight:700;font-size:74px;letter-spacing:4px;color:var(--navy);line-height:1}
  .brand-full{top:131px;font-size:13.5px;font-weight:500;line-height:22px;color:var(--navy);letter-spacing:-.2px}
  .divider{position:absolute;top:217px;height:0;border-top:1px dashed #7d8fb0}
  .divider.left{left:48px;width:169px}
  .divider.right{left:295px;width:168px}
  .brain-icon{position:absolute;left:222px;top:188px;width:66px;height:58px;border-radius:50%;
    background:radial-gradient(circle,#c79a55 0%,#d9b47a 60%,rgba(217,180,122,0) 75%)}
  .question{position:absolute;left:0;width:512px;top:254px;text-align:center;font-weight:400;font-size:26px;line-height:32px;letter-spacing:1.5px;color:var(--navy)}
  .question strong{font-weight:700}
  .question-sub{position:absolute;left:0;width:512px;top:326px;text-align:center;font-size:15px;line-height:20px;color:#111}
  .intro{position:absolute;left:122px;width:683px;top:482px;text-align:center;color:var(--white);font-size:16.5px;line-height:29.5px}
  .section-label{position:absolute;left:0;width:927px;top:589px;text-align:center;color:var(--gold-light);font-size:17px;font-weight:500;letter-spacing:-.2px}
  .card{position:absolute;top:647px;width:263px;height:259px;border-radius:26px;background:linear-gradient(180deg,#a27b3f,#93703a);text-align:center;color:var(--white)}
  .card.c1{left:48px}.card.c2{left:332px}.card.c3{left:616px}
  .card-icon{position:absolute;left:90px;top:38px;width:82px;height:82px;border-radius:50%;background:var(--white)}
  .card-icon svg{position:absolute;left:21px;top:21px}
  .card-title{position:absolute;left:0;width:263px;top:136px;font-weight:400;font-size:15.5px;letter-spacing:1.2px}
  .card-text{position:absolute;left:22px;width:219px;top:166px;font-size:12.3px;font-weight:300;line-height:21.3px}
  .eligible-heading{position:absolute;left:46px;top:955px;font-weight:400;font-size:25px;line-height:38px;letter-spacing:1.5px;color:var(--navy)}
  .eligible-heading strong{font-weight:700;font-size:26px;letter-spacing:2.5px}
  .criteria{position:absolute;left:364px;top:948px;list-style:none;font-size:16.5px;color:#1c2340}
  .criteria li{position:relative;padding-left:36px;line-height:33px;width:530px}
  .criteria li svg{position:absolute;left:0;top:9px}
  .footer{position:absolute;left:0;top:1115px;width:927px;height:85px;background:var(--navy)}
  .footer-gold{position:absolute;left:0;top:0}
  .cta{position:absolute;left:48px;top:11px;font-weight:700;font-size:28.5px;letter-spacing:1.2px;color:var(--white);line-height:40px}
  .cta-sub{position:absolute;left:48px;top:57px;font-weight:700;font-size:12px;letter-spacing:.8px;color:var(--white)}
  .contact{position:absolute;left:419px;top:56px;display:flex;align-items:center;gap:16px;color:var(--gold-light);font-size:14px}
  .comp-label{position:absolute;left:682px;top:13px;font-size:15px;letter-spacing:.6px;color:var(--white)}
  .comp-amount{position:absolute;left:682px;top:33px;font-size:35px;font-weight:800;color:var(--white);letter-spacing:.2px;line-height:42px}
  .code{position:absolute;left:898px;top:70px;font-size:8px;color:var(--white)}
</style>
</head>
<body>
<div class="flyer">
  <div class="hero-photo" role="img" aria-label="Photo of a teenage girl sitting on the floor against a pale wall, hugging her knees"></div>

  <svg class="backdrop" width="927" height="1200" viewBox="0 0 927 1200" aria-hidden="true">
    <defs>
      <linearGradient id="edge" x1="0" x2="1">
        <stop offset="0" stop-color="#c99f61"/>
        <stop offset=".5" stop-color="#f3d394"/>
        <stop offset="1" stop-color="#c99f61"/>
      </linearGradient>
    </defs>
    <path d="M0,405 C120,428 300,410 470,410 C640,411 800,425 927,355 L927,745 C820,790 700,803 463,806 C260,808 110,805 0,796 Z" fill="var(--navy)"/>
    <path d="M0,405 C120,428 300,410 470,410 C640,411 800,425 927,355" fill="none" stroke="url(#edge)" stroke-width="4"/>
  </svg>

  <div class="brand brand-name serif">SOLVE</div>
  <div class="brand brand-full">SEQUOIA OUTLOOK LANTERN VALLEY ECHO<br>STUDY</div>
  <div class="divider left"></div>
  <div class="divider right"></div>
  <div class="brain-icon" role="img" aria-label="Gold line illustration of a brain"></div>

  <h2 class="question serif">ARE YOU THE PARENT OF<br>A CHILD <strong>AGE 10-17?</strong></h2>
  <p class="question-sub">Do they worry or overthink negative<br>emotions?</p>

  <p class="intro">Northbridge University researchers are seeking girls age 10-17 for a study about brain activity in emotions and decision-making and how they relate to puberty, anxiety and depression.</p>
  <p class="section-label">STUDY PARTICIPATION INVOLVES:</p>

  <div class="card c1">
    <div class="card-icon">
      <svg width="40" height="40" viewBox="0 0 40 40" fill="none" stroke="#a57a3c" stroke-width="1.6">
        <rect x="5" y="11" width="24" height="17" rx="1.5"/>
        <path d="M2 32h30l-2-4H4z"/>
        <circle cx="13" cy="18" r="2.6"/>
        <path d="M8.5 25c0-3 2-4.5 4.5-4.5s4.5 1.5 4.5 4.5z"/>
        <rect x="20" y="4" width="17" height="11" rx="1.5"/>
        <path d="M23 8h11M23 11h8"/>
      </svg>
    </div>
    <h3 class="card-title serif">ONE ONE-HOUR INTERVIEW</h3>
    <p class="card-text">One one-hour interview (online or in-person) where your child will discuss their thoughts</p>
  </div>

  <div class="card c2">
    <div class="card-icon">
      <svg width="40" height="40" viewBox="0 0 40 40" fill="none" stroke="#a57a3c" stroke-width="2">
        <path d="M4 8l3 3 5-6M4 20l3 3 5-6"/>
        <circle cx="7.5" cy="32" r="3"/>
        <path d="M16 8h20M16 12h14M16 20h20M16 24h14M16 32h20"/>
      </svg>
    </div>
    <h3 class="card-title serif">ONLINE QUESTIONNAIRES</h3>
    <p class="card-text">Online questionnaires (parent and<br>child)</p>
  </div>

  <div class="card c3">
    <div class="card-icon">
      <svg width="40" height="40" viewBox="0 0 40 40" fill="none" stroke="#a57a3c" stroke-width="1.6">
        <path d="M6 22a14 14 0 1 1 28 0"/>
        <path d="M11 22a9 9 0 1 1 18 0"/>
        <rect x="17" y="4" width="6" height="3" rx="1"/>
        <path d="M14 26l3-8h6l3 8z"/>
        <rect x="9" y="26" width="22" height="4" rx="1"/>
        <path d="M12 30v4h16v-4"/>
      </svg>
    </div>
    <h3 class="card-title serif">ONE TWO-HOUR VISIT</h3>
    <p class="card-text">where your child will complete an MRI scan, answer questions about their puberty stage,</p>
  </div>

  <h2 class="eligible-heading serif">YOUR CHILD<br><strong>MAY BE ELIGIBLE<br>IF THEY:</strong></h2>
  <ul class="criteria">
    <li><svg width="15" height="15" viewBox="0 0 15 15"><circle cx="7.5" cy="7.5" r="7.5" fill="#1c1c1c"/><path d="M4 7.7l2.4 2.3L11 5.3" fill="none" stroke="#fff" stroke-width="1.8"/></svg>Are age 10-17</li>
    <li><svg width="15" height="15" viewBox="0 0 15 15"><circle cx="7.5" cy="7.5" r="7.5" fill="#1c1c1c"/><path d="M4 7.7l2.4 2.3L11 5.3" fill="none" stroke="#fff" stroke-width="1.8"/></svg>Tend to worry or overthink negative thoughts</li>
    <li><svg width="15" height="15" viewBox="0 0 15 15"><circle cx="7.5" cy="7.5" r="7.5" fill="#1c1c1c"/><path d="M4 7.7l2.4 2.3L11 5.3" fill="none" stroke="#fff" stroke-width="1.8"/></svg>Have not been diagnosed with psychosis, learning problems,<br>or autism</li>
  </ul>

  <footer class="footer">
    <svg class="footer-gold" width="927" height="85" viewBox="0 0 927 85" aria-hidden="true">
      <path d="M663,0 H927 V85 H634 Z" fill="var(--gold)"/>
    </svg>
    <h2 class="cta serif">INTERESTED IN PARTICIPATING?</h2>
    <p class="cta-sub serif">WANT MORE INFORMATION? PLEASE CONTACT US!</p>
    <div class="contact">
      <svg width="13" height="10" viewBox="0 0 13 10"><rect width="13" height="10" rx="1" fill="#e9c47f"/><path d="M0.5 1l6 4.3 6-4.3" fill="none" stroke="#0c2350" stroke-width="1.2"/></svg>
      <span>solve@northbridge.edu</span>
    </div>
    <p class="comp-label serif">COMPENSATION</p>
    <p class="comp-amount">UP TO $140</p>
    <span class="code">C58</span>
  </footer>
</div>
</body>
</html>
```